product development company BRVEMKO LLC business card

We need a business card design for a company based in Texas called 'BRVEMKO LLC'. Our first product is a illuminated portable ice chest that is called ' Copper Harbor coolers'. Copper harbor coolers is trademarked. I would like to have the copper harbor trademark somewhere on the card as well as the BRVEMKO LLC name.

Target Market(s)

outdoor industry

Industry/Entity Type

Business

Contact Information for Business Card

i would like to have BRVEMKO LLC logo larger than the Copper harbor coolers logo.

Font styles to use
Serif
Sans Serif

```html
<!DOCTYPE html>
<html lang="en">
<head>
<meta charset="utf-8">
<title>BRVEMKO LLC – Business Card</title>
<link rel="stylesheet" href="https://fonts.googleapis.com/css2?family=Libre+Baskerville:wght@400&display=swap">
<style>
  :root {
    --page-bg: #e9e9e7;
    --card-bg: #ffffff;
    --brand-blue: #1f8fcf;
    --brand-green: #9cc33b;
    --ink-dark: #1c1c1c;
    --serif: "Libre Baskerville", "Times New Roman", serif;
  }
  html, body {
    margin: 0;
    width: 1200px;
    height: 780px;
    overflow: hidden;
    background: var(--page-bg);
  }
  .canvas {
    position: relative;
    width: 1200px;
    height: 780px;
    display: flex;
    align-items: center;
    justify-content: center;
  }
  .card {
    position: relative;
    width: 1000px;
    height: 572px;
    background: var(--card-bg);
    box-shadow: 0 6px 24px rgba(0,0,0,0.12);
    font-family: var(--serif);
  }
  .brand {
    position: absolute;
    left: 70px;
    top: 70px;
    display: flex;
    align-items: flex-start;
    gap: 26px;
  }
  .brand-mark {
    width: 150px;
    height: 150px;
    background: var(--brand-green);
    border-radius: 12px;
  }
  .brand-name {
    display: flex;
    flex-direction: column;
    align-items: center;
    color: var(--brand-blue);
    padding-top: 4px;
  }
  .brand-name .word {
    font-size: 74px;
    letter-spacing: 3px;
    line-height: 1;
  }
  .brand-name .suffix {
    display: flex;
    align-items: center;
    gap: 16px;
    margin-top: 14px;
    font-size: 40px;
    letter-spacing: 4px;
  }
  .brand-name .suffix::before,
  .brand-name .suffix::after {
    content: "";
    width: 150px;
    height: 2px;
    background: var(--brand-green);
  }
  .divider {
    position: absolute;
    left: 250px;
    right: 60px;
    top: 318px;
    height: 2px;
    background: var(--brand-green);
  }
  .person {
    position: absolute;
    right: 70px;
    top: 244px;
    text-align: right;
  }
  .person .name {
    color: var(--brand-blue);
    font-size: 30px;
    letter-spacing: 1px;
  }
  .person .role {
    color: var(--brand-green);
    font-size: 19px;
    margin-top: 2px;
  }
  .product {
    position: absolute;
    right: 70px;
    top: 350px;
    display: flex;
    align-items: center;
    gap: 14px;
    color: var(--ink-dark);
    font-size: 30px;
  }
  .product .dot {
    width: 34px;
    height: 34px;
    border-radius: 50%;
    background: var(--ink-dark);
  }
  .contact-rule {
    position: absolute;
    left: 70px;
    top: 360px;
    width: 2px;
    height: 120px;
    background: var(--brand-green);
  }
  .contact {
    position: absolute;
    left: 110px;
    top: 400px;
    list-style: none;
    margin: 0;
    padding: 0;
    color: var(--brand-blue);
    font-size: 22px;
  }
  .contact li {
    display: flex;
    align-items: center;
    gap: 12px;
    height: 36px;
  }
  .contact svg {
    width: 24px;
    height: 24px;
  }
</style>
</head>
<body>
<main class="canvas">
  <section class="card">
    <div class="brand">
      <div class="brand-mark"></div>
      <div class="brand-name">
        <span class="word">BRVEMKO</span>
        <span class="suffix">LLC</span>
      </div>
    </div>

    <div class="divider"></div>

    <div class="person">
      <div class="name">EMPLOYEE NAME</div>
      <div class="role">Maneger</div>
    </div>

    <div class="product">
      <span class="dot"></span>
      <span>Copper Harbor coolers</span>
    </div>

    <div class="contact-rule"></div>
    <ul class="contact">
      <li>
        <svg viewBox="0 0 24 24" aria-hidden="true"><rect width="24" height="24" rx="2" fill="#9cc33b"/><path d="M7 5l3 0 1 4-2 1a9 9 0 0 0 5 5l1-2 4 1 0 3c0 1-1 2-2 2A13 13 0 0 1 5 7c0-1 1-2 2-2z" fill="#fff"/></svg>
        <span>123 456 7890</span>
      </li>
      <li>
        <svg viewBox="0 0 24 24" aria-hidden="true"><rect width="24" height="24" rx="2" fill="#9cc33b"/><rect x="5" y="7" width="14" height="10" fill="none" stroke="#fff" stroke-width="1.6"/><path d="M5 7l7 6 7-6" fill="none" stroke="#fff" stroke-width="1.6"/></svg>
        <span>your@yourcompany.com</span>
      </li>
      <li>
        <svg viewBox="0 0 24 24" aria-hidden="true"><rect width="24" height="24" rx="2" fill="#9cc33b"/><circle cx="12" cy="12" r="7" fill="none" stroke="#fff" stroke-width="1.5"/><ellipse cx="12" cy="12" rx="3" ry="7" fill="none" stroke="#fff" stroke-width="1.3"/><path d="M5 12h14" stroke="#fff" stroke-width="1.3"/></svg>
        <span>www.yourcompany.com</span>
      </li>
    </ul>
  </section>
</main>
</body>
</html>
```